Accounting firm needing business card / letterhead designed
Marcus L. Trenholm, CPA
marcus@veltrowledger.com
www.veltrowledger.com
842 E Alder Ave Wrenfield, KS 43827
620-562-0974

```html
<!DOCTYPE html>
<html lang="en">
<head>
<meta charset="utf-8">
<title>Veltro Ledger – Business Card</title>
<link rel="stylesheet" href="https://fonts.googleapis.com/css2?family=Open+Sans:wght@400;600&display=swap">
<style>
  :root {
    --navy: #252466;
    --green: #8dc63f;
    --card-white: #ffffff;
    --card-grey: #eeeeee;
    --text: #3a3a3a;
    --backdrop: #e4e1dd;
  }
  * { box-sizing: border-box; margin: 0; padding: 0; }
  html, body { width: 1200px; height: 900px; overflow: hidden; }
  body {
    position: relative;
    background: var(--backdrop);
    font-family: "Open Sans", Arial, sans-serif;
  }
  .card {
    position: absolute;
    overflow: hidden;
    box-shadow: 0 4px 14px rgba(0,0,0,0.12);
  }
  .card-front {
    left: 77px; top: 34px; width: 589px; height: 364px;
    background: var(--card-white);
  }
  .brand-panel {
    position: absolute; left: 0; top: 0; width: 230px; height: 100%;
    background: var(--green);
  }
  .holder-name {
    position: absolute; right: 35px; top: 56px;
    font-size: 20px; font-weight: 600; color: var(--navy);
    text-transform: uppercase; letter-spacing: 0.2px;
  }
  .address {
    position: absolute; right: 37px; top: 178px;
    font-size: 15px; line-height: 22px; color: var(--text); text-align: right;
  }
  .contact-list {
    position: absolute; right: 37px; top: 250px;
    list-style: none; font-size: 15px; line-height: 21.5px; color: var(--text);
  }
  .contact-list li {
    display: flex; justify-content: flex-end; align-items: center; gap: 6px;
  }
  .contact-icon { width: 14px; height: 14px; fill: var(--green); }
  .card-back {
    left: 388px; top: 505px; width: 567px; height: 352px;
    background: var(--card-grey);
    display: flex; align-items: center; justify-content: center; gap: 12px;
    padding-top: 60px;
  }
  .brand-dot { width: 16px; height: 16px; background: var(--green); }
  .brand-name {
    font-size: 40px; font-weight: 600; color: var(--navy);
    text-transform: uppercase; letter-spacing: 2px;
  }
</style>
</head>
<body>
  <section class="card card-front">
    <div class="brand-panel" role="img" aria-label="Brand colour panel"></div>
    <h1 class="holder-name">Marcus L. Trenholm, CPA</h1>
    <p class="address">842 E Alder Ave Wrenfield,<br>KS 43827</p>
    <ul class="contact-list">
      <li>620-562-0974
        <svg class="contact-icon" viewBox="0 0 16 16" aria-hidden="true"><path d="M3.5 1.5l2.5 0 1.2 3.3-1.6 1.2a9 9 0 0 0 4.4 4.4l1.2-1.6 3.3 1.2v2.5c0 .8-.7 1.5-1.5 1.5A12.5 12.5 0 0 1 2 3c0-.8.7-1.5 1.5-1.5z"/></svg>
      </li>
      <li>marcus@veltrowledger.com
        <svg class="contact-icon" viewBox="0 0 16 16" aria-hidden="true"><path d="M1 3.5h14v9H1z M1.5 4l6.5 5 6.5-5" stroke="#fff" stroke-width="1"/></svg>
      </li>
      <li>www.veltrowledger.com
        <svg class="contact-icon" viewBox="0 0 16 16" aria-hidden="true"><circle cx="8" cy="8" r="6.5"/><path d="M1.5 8h13M8 1.5c-2.5 3-2.5 10 0 13M8 1.5c2.5 3 2.5 10 0 13" stroke="#fff" stroke-width="0.9" fill="none"/></svg>
      </li>
    </ul>
  </section>

  <section class="card card-back">
    <span class="brand-dot" aria-hidden="true"></span>
    <span class="brand-name">Veltro Ledger</span>
  </section>
</body>
</html>
```